Wandering Rooms Stationary Set

Wandering Rooms is a bespoke interior design firm set to provide services to VIP clients with elegance and minimalism is the main theme for our stationary set. We require a full stationary set covering A4 letterhead, A4 & A3 envelopes, business cards, USB's, CDs, email signature and any other item the designer sees fit. logo is already designed and finalized, and we require the designer to use it as is without modifying the logo.

Address to be used on letterhead / business cards ...etc shall be as follows:

Phone : +971 2 518 2047
P.O. Box : 309186
Address: Block C&D, Bldg. 47, Court 12, Abu Dhabi, United Arab Emirates
Website: www.wanderingrooms-example.com

Target Market(s)

VIP Clients

Industry/Entity Type

Interior Design

Font styles to use
Other font styles liked:
• something to be unique

Colors

Designer to choose colors to be used in the design.

Requirements
Must have
• Elegant, minimalistic
Nice to have
• Simple yet elegant design having a sharp yet clean cut format
Should not have
• No additional colours, just colours that are used in the logo (silver, black or gold)

```html
<!DOCTYPE html>
<html lang="en">
<head>
<meta charset="utf-8">
<title>Wandering Rooms Stationery</title>
<link rel="stylesheet" href="https://fonts.googleapis.com/css2?family=Cormorant+Garamond:wght@500&family=Open+Sans:wght@400;700&display=swap">
<style>
  :root {
    --backdrop: #d9d9d9;
    --paper: #ffffff;
    --paper-shade: #f1f1f3;
    --ink: #111111;
    --ink-soft: #333333;
    --silver: #b9b9b9;
    --graphite: #6e6e6e;
    --faint: #e2e2e4;
  }
  * { box-sizing: border-box; margin: 0; padding: 0; }
  html, body { width: 1200px; height: 800px; overflow: hidden; }
  body {
    background: var(--backdrop);
    position: relative;
    font-family: "Open Sans", sans-serif;
    color: var(--ink-soft);
  }

  /* Letterhead */
  .letterhead {
    position: absolute;
    left: 350px; top: 47px;
    width: 500px; height: 706px;
    background: linear-gradient(180deg, var(--paper) 0%, var(--paper) 70%, var(--paper-shade) 100%);
    overflow: hidden;
  }
  .letterhead__swoosh { position: absolute; top: 0; left: 0; }
  .brand-name {
    font-family: "Cormorant Garamond", serif;
    font-weight: 500;
    color: var(--ink);
    letter-spacing: 0.14em;
    text-transform: uppercase;
    line-height: 1.15;
  }
  .letterhead__brand {
    position: absolute; left: 62px; top: 48px;
    font-size: 22px;
    width: 180px;
  }
  .letterhead__contacts {
    position: absolute; left: 62px; top: 120px;
    font-family: "Cormorant Garamond", serif;
    font-size: 7.5px; color: var(--ink);
    line-height: 12px;
  }
  .letterhead__web { font-family: "Open Sans", sans-serif; font-weight: 700; font-size: 7px; }
  .letterhead__contacts .label { font-weight: 500; margin-right: 5px; }
  .letterhead__contacts .gap { margin-right: 12px; }
  .letterhead__date {
    position: absolute; right: 64px; top: 175px;
    font-size: 7px;
  }
  .letterhead__body {
    position: absolute; left: 63px; top: 243px; width: 380px;
    font-size: 7px; line-height: 16px;
  }
  .letterhead__body p { margin-bottom: 16px; }
  .signoff { position: absolute; left: 63px; top: 532px; }
  .signoff__signature {
    width: 80px; height: 20px;
    background: linear-gradient(90deg, #ececec, #f6f6f6);
    margin-bottom: 4px;
  }
  .signoff__name { font-size: 7.5px; font-weight: 700; color: var(--ink); line-height: 9px; }
  .signoff__role { font-size: 7px; line-height: 9px; }
  .letterhead__watermark {
    position: absolute; right: 62px; top: 600px;
    font-size: 28px; color: var(--faint); text-align: right; width: 260px;
  }
  .letterhead__footer {
    position: absolute; left: 0; bottom: 0; width: 100%; height: 26px;
    background: var(--ink);
    color: var(--paper);
    font-family: "Cormorant Garamond", serif;
    font-size: 7.5px;
    display: flex; align-items: center; justify-content: center;
  }

  /* Business cards */
  .business-card {
    position: absolute;
    left: 880px; width: 210px; height: 132px;
    background: var(--paper);
    display: flex; align-items: center; justify-content: center;
  }
  .business-card--front { top: 56px; }
  .business-card--back { top: 232px; background: #f4f4f6; }
  .business-card .brand-name { font-size: 16px; text-align: center; }
</style>
</head>
<body>

<section class="letterhead">
  <svg class="letterhead__swoosh" width="500" height="706" viewBox="0 0 500 706" aria-hidden="true">
    <path d="M175,0 H500 V232 C470,125 360,25 175,0 Z" fill="var(--silver)"/>
    <path d="M205,0 H500 V212 C468,118 370,22 205,0 Z" fill="var(--graphite)"/>
    <path d="M250,0 H500 V178 C462,92 380,18 250,0 Z" fill="var(--ink)"/>
  </svg>

  <div class="letterhead__brand brand-name">Wandering Rooms</div>

  <div class="letterhead__contacts">
    <div class="letterhead__web">www.wanderingrooms-example.com</div>
    <div><span class="label">E:</span><span class="gap">info@wanderingrooms-example.com</span><span class="label">P:</span>+971 2 518 2047</div>
  </div>

  <div class="letterhead__date">Date, 10 September, 2019</div>

  <div class="letterhead__body">
    <p>This is a sample letter that has been placed to demonstrate typing format (Your Company), letterhead design. When positioned properly, it will serve to work in harmony with all other elements letterhead. This letterhead design is meant to project an image</p>
    <p>This letterhead design is meant project an image of professionalism reliability. By using simple alignment we have created a very spacious feeling. The simplicity suggest strength the spaciousness contributes to aesthetics the layout. These basic qualities along with the (Your Company)</p>
    <p>look and helps reinforce the (Your Company) brand. letterhead design is meant to project an image of design. When positioned properly, it will serve to work in harmony all the other elements letterhead. professionalism and reliability.</p>
    <p>This letterhead design is based on the (Form of your logo) form (Your Company) logo. Each element we have created a very spacious feeling. The simplicity suggests strength the spaciousness contribute part of the (Form of your logo).</p>
  </div>

  <div class="signoff">
    <div class="signoff__signature" role="img" aria-label="Handwritten signature of Laila Varen"></div>
    <div class="signoff__name">Laila Varen</div>
    <div class="signoff__role">Manager</div>
  </div>

  <div class="letterhead__watermark brand-name">Wandering Rooms</div>

  <footer class="letterhead__footer">Block C&amp;D, Bldg. 47, Court 12, Abu Dhabi, United Arab Emirates</footer>
</section>

<section class="business-card business-card--front">
  <div class="brand-name">Wandering<br>Rooms</div>
</section>

<section class="business-card business-card--back">
  <div class="brand-name">Wandering<br>Rooms</div>
</section>

</body>
</html>
```